Business Card for beauty technology startup

Design Glimora Business Card for a Beauty, based on the website identity and colors (https://www.glimora-example.com).
Glimora is a beauty tech startup that gathers helpful product info for beauty lovers and consumers (such as availability on stores, price range and product reviews) for makeup products. The card design must be young, colorful but clean, and very modern.

Target Market(s)

woman, 15-35

Industry/Entity Type

Cosmetics

Contact Information for Business Card

Full Name, address, phone

Font styles to use
Other font styles liked:
• Advent Pro

Colors
e34297
86cfc6
ffffff
5c5c5c
e8e8e8
e667a6
b2b2b2

Requirements
Must have
• One full colored side with a creative design and another with card info
• Use Color palette: #95C5C5 and/or #D38AA5
• Use fonts: Advent Pro
• Use website identity: https://www.glimora-example.com
Nice to have
• If needed extra font: Roboto

```html
<!DOCTYPE html>
<html lang="en">
<head>
<meta charset="utf-8">
<title>Glimora Business Card</title>
<link href="https://fonts.googleapis.com/css2?family=Advent+Pro:wght@300;400&family=Roboto:wght@400;500&family=Quicksand:wght@400;500&display=swap" rel="stylesheet">
<style>
  :root{
    --page-bg:#e8e8e8;
    --plum:#6b5a65;
    --plum-deep:#5f4f5a;
    --mauve:#b97d9a;
    --mauve-strong:#a56e8c;
    --ink:#4f4a4e;
    --white:#ffffff;
  }
  *{margin:0;padding:0;box-sizing:border-box}
  html,body{width:1200px;height:1155px;overflow:hidden;background:var(--page-bg)}
  .stage{position:relative;width:1200px;height:1155px}
  .card{position:absolute;left:218px;width:758px;height:434px;border-radius:32px;overflow:hidden}
  .card-front{top:134px;background:var(--plum)}
  .card-back{top:596px;background:var(--white)}

  .product-shape{position:absolute;background:var(--plum-deep);opacity:.55;border-radius:6px}
  .product-lipstick{left:56px;top:34px;width:78px;height:352px;border-radius:30px 30px 4px 4px}
  .product-mascara{left:598px;top:54px;width:104px;height:332px}

  .front-brand{position:absolute;left:0;right:0;top:168px;display:flex;align-items:center;justify-content:center;gap:18px}
  .front-brand .brand-dot{width:40px;height:40px;border:3px solid var(--white);border-radius:50%}
  .front-brand .brand-name{font-family:"Advent Pro",sans-serif;font-weight:400;font-size:64px;letter-spacing:4px;color:var(--white);line-height:1}

  .social-row{position:absolute;left:0;right:0;top:366px;display:flex;justify-content:center;gap:13px}
  .social-dot{width:28px;height:28px;border-radius:50%;background:var(--white)}

  .portrait{position:absolute;left:6px;top:12px;width:256px;height:421px;
    background:linear-gradient(180deg,#efe6e0 0%,#ebe8e6 55%,#e4e4e4 72%,#3a4442 74%,#2f3836 100%);
    border-radius:20px 0 0 24px}

  .back-brand{position:absolute;right:41px;top:64px;display:flex;align-items:center;gap:36px}
  .back-brand .brand-dot{width:84px;height:84px;border:3px solid var(--mauve);border-radius:50%}
  .back-brand .brand-name{font-family:"Advent Pro",sans-serif;font-weight:300;font-size:66px;letter-spacing:8px;color:var(--mauve);line-height:1}

  .contact{position:absolute;right:41px;top:188px;text-align:right;color:var(--ink)}
  .person-name{font-family:"Roboto",sans-serif;font-weight:500;font-size:24px;letter-spacing:.5px;color:var(--mauve-strong);line-height:1}
  .person-role{font-family:"Roboto",sans-serif;font-size:15px;letter-spacing:1px;margin-top:10px;line-height:1}
  .address{font-family:"Quicksand",sans-serif;font-weight:500;font-size:20px;line-height:28px;margin-top:16px}
  .lines{margin-top:8px;font-family:"Quicksand",sans-serif;font-weight:500;font-size:20px;line-height:27.5px}
  .line{display:flex;justify-content:flex-end;align-items:center;gap:10px}
  .line svg{width:12px;height:12px;flex:none}
</style>
</head>
<body>
<div class="stage">

  <section class="card card-front" aria-label="Card front">
    <div class="product-shape product-lipstick" role="img" aria-label="Faint lipstick product photo"></div>
    <div class="product-shape product-mascara" role="img" aria-label="Faint mascara product photo"></div>
    <div class="front-brand">
      <span class="brand-dot"></span>
      <span class="brand-name">Glimora</span>
    </div>
    <div class="social-row" aria-label="Social profiles">
      <span class="social-dot"></span><span class="social-dot"></span><span class="social-dot"></span><span class="social-dot"></span>
    </div>
  </section>

  <section class="card card-back" aria-label="Card back">
    <div class="portrait" role="img" aria-label="Photo of a model in a sheer white blouse and dark skirt"></div>
    <div class="back-brand">
      <span class="brand-dot"></span>
      <span class="brand-name">GLIMORA</span>
    </div>
    <div class="contact">
      <div class="person-name">LENA MARWICK</div>
      <div class="person-role">OWNER</div>
      <div class="address">48 Palm Reed Lane<br>Tequesta, FL 33469</div>
      <div class="lines">
        <div class="line">561.555.0148
          <svg viewBox="0 0 12 12"><path d="M3 1.5c-.8.3-1.5 1-1.3 2.2.5 2.8 3.2 5.9 6.2 6.6 1 .2 1.6-.3 2-1l-1.7-1.5-1.2.8C5.8 8 4.4 6.6 3.8 5.3l.8-1.1z" fill="var(--mauve)"/></svg>
        </div>
        <div class="line">info@glimora-example.com
          <svg viewBox="0 0 12 12"><rect x="1" y="2.5" width="10" height="7" rx="1" fill="none" stroke="var(--mauve)" stroke-width="1.2"/><path d="M1.5 3l4.5 3.5L10.5 3" fill="none" stroke="var(--mauve)" stroke-width="1.1"/></svg>
        </div>
        <div class="line">www.glimora-example.com
          <svg viewBox="0 0 12 12"><circle cx="6" cy="6" r="5" fill="none" stroke="var(--mauve)" stroke-width="1.1"/><path d="M1 6h10M6 1c-2.2 2.8-2.2 7.2 0 10M6 1c2.2 2.8 2.2 7.2 0 10" fill="none" stroke="var(--mauve)" stroke-width=".9"/></svg>
        </div>
      </div>
    </div>
  </section>

</div>
</body>
</html>
```